International business needs business cards

Our company, DRV Ventures Inc. is in the business of supplying a range construction products with particular emphasis on CEMENT. We have developed our own brand - TORVAN SUPPLIES - with which to infiltrate the market. We are launching our brand of cement (TORVAN Type IS Cement) into the Caribbean which is unlike anything this market has ever seen. A monopoly has existed here for the past 60-odd years and the market has now opened to allow the importation of other brands and consumers are anxious and ready for change/improvement. We are very excited to be launching and want to make a great first impression. We will be conducting workshops and seminars (from government level to the hardware store owners) and we want our business card to give us the strong, confident introduction that we need.

Target Market(s)

construction; builders; engineers; home owners

Industry/Entity Type

Construction

Contact Information for Business Card

Marisol Depree
CEO
cell # 1 555 4180736
Ground floor,Lindell Plaza Suite 2734
George Town,Grand Cayman
Cayman Islands,KY1-4823
EMAIL: m.depree@drvventuresinc.example
web site drvventuresinc.example

COMPANY: skype info drv.ventures.example

second card
Yvette Brannock-Depree
CFO
CELL# 1 555 607 3941
George Town,Grand Cayman
Cayman Islands,KY1-4823
EMAIL: y.brannockdepree@drvventuresinc.example
website drvventuresinc.example

Requirements
Must have
• Business cards must display BOTH logos - DRV is the company and TORVAN is the brand.

```html
<!DOCTYPE html>
<html lang="en">
<head>
<meta charset="utf-8">
<title>DRV Ventures Inc. — Business Card</title>
<link rel="stylesheet" href="https://fonts.googleapis.com/css2?family=Open+Sans:wght@400;600;700&display=swap">
<style>
  :root {
    --canvas-bg: #8e8e8c;
    --card-black: #0b0b0b;
    --card-black-soft: #1c1c1c;
    --brand-red: #7e1419;
    --accent-copper: #b8774f;
    --text-white: #f4f4f4;
    --text-grey: #a9a9a9;
    --rule: #2e2e2e;
  }
  * { box-sizing: border-box; margin: 0; padding: 0; }
  html, body { width: 1200px; height: 900px; overflow: hidden; }
  body {
    background: var(--canvas-bg);
    font-family: "Open Sans", Arial, sans-serif;
    display: flex;
    flex-direction: column;
    align-items: center;
    justify-content: center;
    gap: 40px;
  }
  .card {
    position: relative;
    width: 640px;
    height: 366px;
    background: radial-gradient(ellipse at 55% 45%, var(--card-black-soft), var(--card-black) 75%);
    color: var(--text-white);
    overflow: hidden;
  }

  /* Back of card */
  .card-back { display: flex; align-items: center; justify-content: center; gap: 18px; }
  .brand-square { width: 110px; height: 110px; background: var(--brand-red); }
  .card-back .company-name { font-size: 30px; font-weight: 700; color: var(--text-white); }

  /* Front of card */
  .holder { position: absolute; left: 44px; top: 62px; }
  .holder-name { font-size: 21px; font-weight: 700; color: var(--accent-copper); }
  .holder-title { font-size: 15px; color: var(--text-white); }

  .company-lockup { position: absolute; right: 36px; top: 44px; display: flex; align-items: center; gap: 12px; }
  .company-lockup .brand-square { width: 62px; height: 62px; }
  .company-lockup .company-name { font-size: 24px; font-weight: 700; color: var(--text-white); }

  .divider { position: absolute; left: 44px; right: 36px; top: 128px; height: 1px; background: var(--rule); }

  .product-brand {
    position: absolute; left: 44px; top: 190px;
    font-size: 20px; font-weight: 700; letter-spacing: 1px; color: var(--text-grey);
  }

  .contact { position: absolute; right: 36px; top: 150px; text-align: right; font-size: 15px; line-height: 1.4; }
  .contact-row { display: flex; align-items: center; justify-content: flex-end; gap: 10px; }
  .contact-row .icon { width: 14px; height: 14px; flex: none; }
  .icon-spacer { width: 14px; flex: none; }
  .address { margin-top: 2px; }
</style>
</head>
<body>

  <section class="card card-back" aria-label="Business card back">
    <div class="brand-square"></div>
    <span class="company-name">DRV Ventures Inc.</span>
  </section>

  <section class="card card-front" aria-label="Business card front">
    <div class="holder">
      <p class="holder-name">Marisol Depree</p>
      <p class="holder-title">CEO</p>
    </div>

    <div class="company-lockup">
      <div class="brand-square"></div>
      <span class="company-name">DRV Ventures Inc.</span>
    </div>

    <div class="divider"></div>

    <p class="product-brand">TORVAN SUPPLIES</p>

    <div class="contact">
      <p class="contact-row">1 555 4180736
        <svg class="icon" viewBox="0 0 14 14" aria-hidden="true"><rect x="3.5" y="1" width="7" height="12" rx="1.2" fill="none" stroke="var(--accent-copper)" stroke-width="1.3"/><circle cx="7" cy="11" r="0.8" fill="var(--accent-copper)"/></svg>
      </p>
      <p class="contact-row">m.depree@drvventuresinc.example
        <svg class="icon" viewBox="0 0 14 14" aria-hidden="true"><rect x="1" y="3" width="12" height="8" fill="var(--accent-copper)"/><path d="M1 3 L7 8 L13 3" fill="none" stroke="var(--card-black)" stroke-width="1"/></svg>
      </p>
      <p class="contact-row">www.drvventuresinc.example
        <svg class="icon" viewBox="0 0 14 14" aria-hidden="true"><circle cx="7" cy="7" r="6" fill="var(--accent-copper)"/><path d="M1 7 H13 M7 1 C4 4 4 10 7 13 M7 1 C10 4 10 10 7 13" fill="none" stroke="var(--card-black)" stroke-width="0.9"/></svg>
      </p>
      <div class="address">
        <p class="contact-row">Ground floor, Lindell Plaza Suite<span class="icon-spacer"></span></p>
        <p class="contact-row">2734 George Town, Grand Cayman<span class="icon-spacer"></span></p>
        <p class="contact-row">Cayman Islands, KY1-4823<span class="icon-spacer"></span></p>
      </div>
    </div>
  </section>

</body>
</html>
```